need corporate, modern business card created for Consulting Company

I need a slick business card using elements from my website, as well as, integrating my pixelforge-created logo (see files).

The business card needs to be:
1. Corporate and modern
2. Clean and professional

I've included a PSD with the logo/icon that you can use to create it. Feel free to try a metallic finish on the logo, make it bigger/small, underlay it. Whatever you need to do to make my card stand out.

Try a black background, or white background or gray.

The idea is for my card to be memorable as well as professional and corporate.

Target Market(s)

Corporate business in the US and Canada.

Industry/Entity Type

Business

Contact Information for Business Card

Commerce Advancing Methods
Martin Coles, Senior Partner
office: 1 877 555 0143
mobile: 1 519 555 0172
website: http://www.brightvale.example

Requirements
Must have
• Card-related information
• corporate, yet modern
• clean and professional
• incorporate the icon only
• must have an editable form when complete!
Nice to have
• metallic icon might be cool
• try it with white or black

```html
<!DOCTYPE html>
<html lang="en">
<head>
<meta charset="utf-8">
<title>Brightvale Business Card</title>
<link href="https://fonts.googleapis.com/css2?family=Exo+2:wght@400;500;600&display=swap" rel="stylesheet">
<style>
  :root {
    --canvas: #e6e6e4;
    --card-black: #1f1f20;
    --panel-gray: #a9abae;
    --accent-blue: #2f6db8;
    --ink-dark: #2b2b2d;
    --ink-light: #ffffff;
  }
  * { box-sizing: border-box; margin: 0; padding: 0; }
  html, body {
    width: 1200px; height: 803px; overflow: hidden;
    background: var(--canvas);
    font-family: "Exo 2", sans-serif;
  }
  .sheet { position: relative; width: 1200px; height: 803px; }
  .card {
    position: absolute; top: 246px;
    width: 540px; height: 310px;
    background: var(--card-black);
    overflow: hidden;
    box-shadow: 0 6px 18px rgba(0,0,0,0.18);
  }
  .card--front { left: 40px; }
  .card--back  { left: 620px; }
  .card-shapes { position: absolute; inset: 0; }
  .brand {
    position: absolute; display: flex; align-items: center; gap: 10px;
    font-weight: 600; font-size: 40px; letter-spacing: 0.5px;
    color: var(--accent-blue); line-height: 1;
  }
  .brand-mark { width: 14px; height: 14px; background: var(--accent-blue); }
  .card--front .brand { left: 52px; top: 196px; }
  .card--back .brand { left: 40px; top: 150px; font-size: 34px; }
  .band-url {
    position: absolute; left: 520px; top: 16px;
    transform-origin: 0 0; transform: rotate(90deg);
    color: var(--ink-light); font-size: 11px; letter-spacing: 0.6px; white-space: nowrap;
  }
  .holder { position: absolute; left: 318px; top: 70px; color: var(--ink-dark); }
  .holder-name { font-size: 22px; font-weight: 500; letter-spacing: 1.5px; text-transform: uppercase; }
  .holder-title { font-size: 10px; letter-spacing: 1.2px; margin-top: 4px; text-transform: uppercase; }
  .contact-list { position: absolute; left: 312px; top: 146px; list-style: none; color: var(--ink-dark); font-size: 11px; }
  .contact-list li { display: flex; align-items: flex-start; gap: 8px; margin-bottom: 7px; line-height: 14px; }
  .contact-icon { width: 14px; height: 14px; flex: none; }
</style>
</head>
<body>
<main class="sheet">
  <section class="card card--front" aria-label="Card front">
    <svg class="card-shapes" viewBox="0 0 540 310" aria-hidden="true">
      <path d="M478 0 H540 V310 H506 V72 Q506 22 478 0 Z" fill="var(--accent-blue)"/>
    </svg>
    <div class="brand"><span class="brand-mark"></span>brightvale</div>
    <div class="band-url">www.brightvale.example</div>
  </section>

  <section class="card card--back" aria-label="Card back">
    <svg class="card-shapes" viewBox="0 0 540 310" aria-hidden="true">
      <path d="M290 310 V58 Q290 0 350 0 H540 V310 Z" fill="var(--panel-gray)"/>
      <path d="M470 0 H540 V310 H508 V62 Q508 16 470 0 Z" fill="var(--accent-blue)"/>
      <rect x="290" y="82" width="12" height="32" fill="var(--accent-blue)"/>
    </svg>
    <div class="brand"><span class="brand-mark"></span>brightvale</div>
    <div class="holder">
      <div class="holder-name">Martin Coles</div>
      <div class="holder-title">General Manager</div>
    </div>
    <ul class="contact-list">
      <li><svg class="contact-icon" viewBox="0 0 14 14" aria-hidden="true"><circle cx="7" cy="7" r="6.3" fill="none" stroke="var(--ink-dark)"/><path d="M4.5 4 L6 3.8 L6.6 5.6 L5.7 6.2 Q6.5 7.8 7.8 8.4 L8.4 7.5 L10.1 8.1 L10 9.6 Q6 10 4.5 4 Z" fill="var(--ink-dark)"/></svg>1 877 555 0143</li>
      <li><svg class="contact-icon" viewBox="0 0 14 14" aria-hidden="true"><circle cx="7" cy="7" r="6.3" fill="none" stroke="var(--ink-dark)"/><rect x="5" y="3.5" width="4" height="7" rx="0.8" fill="none" stroke="var(--ink-dark)"/></svg>1 519 555 0172</li>
      <li><svg class="contact-icon" viewBox="0 0 14 14" aria-hidden="true"><circle cx="7" cy="7" r="6.3" fill="none" stroke="var(--ink-dark)"/><rect x="4" y="4.8" width="6" height="4.4" fill="var(--ink-dark)"/><path d="M4 4.8 L7 7.4 L10 4.8" fill="none" stroke="var(--panel-gray)" stroke-width="0.8"/></svg>martin@brightvale.example</li>
      <li><svg class="contact-icon" viewBox="0 0 14 14" aria-hidden="true"><circle cx="7" cy="7" r="6.3" fill="none" stroke="var(--ink-dark)"/><circle cx="7" cy="7" r="3.6" fill="none" stroke="var(--ink-dark)" stroke-width="0.8"/><path d="M3.4 7 H10.6 M7 3.4 V10.6" stroke="var(--ink-dark)" stroke-width="0.8"/></svg>www.brightvale.example</li>
      <li><svg class="contact-icon" viewBox="0 0 14 14" aria-hidden="true"><circle cx="7" cy="7" r="6.3" fill="none" stroke="var(--ink-dark)"/><path d="M7 10.5 L4.8 6.8 A2.4 2.4 0 1 1 9.2 6.8 Z" fill="var(--ink-dark)"/><circle cx="7" cy="5.8" r="0.9" fill="var(--panel-gray)"/></svg><span>42 Harbour Road,<br>Suite 300 North</span></li>
    </ul>
  </section>
</main>
</body>
</html>
```